Business Card and Letterhead for Pimlu - modern real estate business

I need a double sided business card design for Pimlu. Please see business card brief here https://files.trelvonadocs.com/sheet/r/7QzTmWbaXLJnoPEd-kRyUgFhHsstbvCe2qfoMxDa_pz/view?mode=shared

Please feel free to design the business cards however you feel best. I am happy to give some creative freedoms and then provide feedback from there.

Please then also create a letterhead to match the business card design

Colors

Designer to choose colors to be used in the design.

Requirements
Must have
• Must be a modern, elegant business card which looks very professional

```html
<!DOCTYPE html>
<html lang="en">
<head>
<meta charset="utf-8">
<title>Pimlu Business Card</title>
<link rel="stylesheet" href="https://fonts.googleapis.com/css2?family=Raleway:wght@400;600&family=Fira+Sans:wght@400&display=swap">
<style>
  :root {
    --bg: #4a4a4c;
    --red: #d90512;
    --black: #000000;
    --white: #ffffff;
    --photo-sky: #c9d3d6;
    --photo-leaf: #5d7a3c;
    --photo-warm: #b9b25a;
  }
  * { margin: 0; padding: 0; box-sizing: border-box; }
  html, body {
    width: 1200px; height: 865px; overflow: hidden;
    background: var(--bg);
  }
  .stage {
    position: relative; width: 1200px; height: 865px;
    display: flex; justify-content: center; align-items: center; gap: 60px;
  }
  .card {
    position: relative; width: 340px; height: 650px; overflow: hidden;
    background: var(--black);
  }
  /* Front */
  .card-front { background: var(--red); }
  .portrait {
    position: absolute; left: 0; top: 0; width: 100%; height: 150px;
    background: linear-gradient(160deg, var(--photo-sky) 0%, var(--photo-leaf) 55%, var(--photo-warm) 100%);
  }
  .agent-name {
    position: absolute; left: 25px; top: 178px;
    font-family: "Raleway", sans-serif; font-weight: 600; font-size: 38px;
    color: var(--white);
  }
  .agent-title {
    position: absolute; left: 25px; top: 234px;
    font-family: "Raleway", sans-serif; font-weight: 400; font-size: 18px;
    color: var(--white);
  }
  .contact-list { position: absolute; left: 25px; top: 308px; list-style: none; }
  .contact-item {
    display: flex; align-items: flex-start; gap: 17px; margin-bottom: 14px;
    font-family: "Fira Sans", sans-serif; font-size: 18px; line-height: 26px;
    color: var(--white);
  }
  .contact-item svg { flex: none; width: 22px; height: 22px; margin-top: 2px; }
  .footer-band { position: absolute; left: 0; bottom: 0; width: 340px; height: 170px; }
  .brand-name {
    position: absolute; left: 0; right: 0;
    text-align: center;
    font-family: "Raleway", sans-serif; font-weight: 600; font-size: 42px;
    letter-spacing: 2px; color: var(--red);
  }
  .card-front .brand-name { top: 546px; }
  /* Back */
  .card-back .brand-name { top: 296px; }
  .web-icon { position: absolute; left: 158px; top: 548px; width: 24px; height: 24px; }
  .web-address {
    position: absolute; left: 0; right: 0; top: 588px; text-align: center;
    font-family: "Fira Sans", sans-serif; font-size: 18px; color: var(--white);
  }
</style>
</head>
<body>
<main class="stage">
  <section class="card card-front">
    <div class="portrait" role="img" aria-label="Portrait photo of the agent outdoors with trees and a valley view"></div>
    <h1 class="agent-name">Liam Carter</h1>
    <p class="agent-title">Licenced Real Estate Agent</p>
    <ul class="contact-list">
      <li class="contact-item">
        <svg viewBox="0 0 24 24" aria-hidden="true"><path fill="#fff" d="M6.6 10.8a15.1 15.1 0 0 0 6.6 6.6l2.2-2.2a1 1 0 0 1 1-.25 11.4 11.4 0 0 0 3.6.57 1 1 0 0 1 1 1V20a1 1 0 0 1-1 1A17 17 0 0 1 3 4a1 1 0 0 1 1-1h3.5a1 1 0 0 1 1 1c0 1.25.2 2.45.57 3.57a1 1 0 0 1-.25 1z"/></svg>
        <span>0412 555 019</span>
      </li>
      <li class="contact-item">
        <svg viewBox="0 0 24 24" aria-hidden="true"><path fill="#fff" d="M3 5h18v14H3z"/><path fill="none" stroke="#d90512" stroke-width="2" d="M3 6l9 7 9-7"/></svg>
        <span>liam@pimlu.com</span>
      </li>
      <li class="contact-item">
        <svg viewBox="0 0 24 24" aria-hidden="true"><path fill="#fff" d="M8 3h2v18H8z"/><path fill="#fff" d="M10 3l7 3-7 3z"/><rect x="5" y="19" width="8" height="2" fill="#fff"/></svg>
        <span>PO Box 1180<br>Ashgrove NSW 2790</span>
      </li>
    </ul>
    <svg class="footer-band" viewBox="0 0 340 170" preserveAspectRatio="none" aria-hidden="true">
      <path fill="#000" d="M0 15 H236 Q244 15 248 9 Q253 3 260 3 Q267 3 272 9 Q276 15 284 15 H340 V170 H0 Z"/>
    </svg>
    <p class="brand-name">PIMLU</p>
  </section>

  <section class="card card-back">
    <p class="brand-name">PIMLU</p>
    <svg class="web-icon" viewBox="0 0 24 24" aria-hidden="true" fill="none" stroke="#d90512" stroke-width="1.8">
      <circle cx="12" cy="12" r="9"/>
      <ellipse cx="12" cy="12" rx="4" ry="9"/>
      <path d="M3 12h18M5 7h14M5 17h14"/>
    </svg>
    <p class="web-address">www.pimlu.com</p>
  </section>
</main>
</body>
</html>
```